Boutique startup consulting

Hello,
Me and my partner are starting a boutique consulting/ "venturing for startup" firm and want to make professional looking slides. The point of these slide are to attract Automakers's venture arms to collaborate with us. We are hoping to win clients with this presentation.

Acceptance criteria:
1. You put beautiful designs where-ever you can and make the attached slides look professional. Full freedom in designing the slides. You are the artist, please create some magic
2. The style should be innovative and state of the art. It should be with colourful designs
3. The slides should be very professional
4. We are unsure of how to present our previous experience. Please help us out
5. The first slide has gray background. you may use the original colored image and tweak it

Here is out website:
https://www.talvora-partners.net/

Can you please ensure that the slides are presented in the following format?

PRESENTATION
1. Starting Masterslide
2. Customized Starting Masterslide (with Topic + Customer Logo, for eg. Smart City & KDR)
3. Service Categories Masterslide /Overview ( we have 5 Categories which are shown by icon and buzzword, see https://www.talvora-partners.net/live/research-strategy/research-strategy.aspx, this is for eg. the Overview for the categorie “Research &Strategy”. We have 2-4 Icon per Category, other categories are Business Development,Venture Building, Expansion Advisory, Sustainable Due Diligence , see webside)
4. Subcategories & Description Masterslide
o We have 15 Subcategories, the Masterslide should just show the Icon and then 1-2 square for description with bullets, f.ex. https://www.talvora-partners.net/live/expansion-advisory-feasibility-analysis/feasibility-analysis.aspx
5. Team Presenting Masterslide
o Not like Website, a Masterslide where each Teammember can present him self, in bullets with Education/Business Experience/ other awards/distinction AND in Text bubbles like “Experiences and hands-on Business developer”
6. Contact ( closing Chart with contact data, liked in etc.)
7. Masterslide (free for individual content)
o Just a slide with the CI framework which can be used as Masterslide for other charts like

8. PROPOSAL Masterslide (like customized starting slide, but Proposal)
9. Background Masterslide (Text)
o A textual description
10. Value Proposition & Goals Masterslide (Text & Bullets)
o V P will be textual so for eg. text frame; Goals with 2-4 squares (text/Bullets) for sub-goals and including the tasks for these goals in bullets
11. Milestones & Timing Masterslide (Timeline , Squares & text)
o Timeline, for eg. 6 Month project, where we have 8 tasks with starting and ending
12. Free MAsterslide /Proposal
o Where we can add charts to the proposal like Conditions or Contact

To Add:
- Logo colour description
- Picture and Icons ( so they don’t need to buy new pics or look for them)

Requirements
Must have
• Please check out the slides and make them presentable

```html
<!DOCTYPE html>
<html lang="en">
<head>
<meta charset="utf-8">
<title>Our Services – Research &amp; Strategy</title>
<link href="https://fonts.googleapis.com/css2?family=Fira+Sans:wght@400;500;600;700&display=swap" rel="stylesheet">
<style>
  :root{
    --lime:#a6c83a;
    --olive:#8ba446;
    --heading-green:#88a83c;
    --panel-grey:#f4f3f1;
    --ink:#232323;
    --ink-soft:#4d4d4d;
    --bar-dark:#454545;
    --white:#ffffff;
    --icon-tint:#c9dc8c;
  }
  *{margin:0;padding:0;box-sizing:border-box}
  html,body{width:1200px;height:675px;overflow:hidden;background:var(--white)}
  body{font-family:"Fira Sans",sans-serif;color:var(--ink)}
  .slide{position:relative;width:1200px;height:675px;overflow:hidden;background:var(--white)}

  /* service navigation */
  .service-nav{position:absolute;left:0;top:0;width:330px;height:675px;background:var(--lime)}
  .service-nav__title{position:absolute;left:81px;top:44px;font-size:26px;font-weight:600;letter-spacing:2px;color:var(--white)}
  .service-nav__rule{position:absolute;left:0;top:82px;width:281px;height:2px;background:var(--white)}
  .service-item{position:absolute;left:0;width:336px;display:flex;align-items:center;color:var(--white);font-size:20px;font-weight:500;line-height:23px}
  .service-item--active{background:var(--olive)}
  .service-item__icon{width:36px;height:40px;margin-left:74px;margin-right:14px;flex:none}
  .service-divider{position:absolute;left:75px;width:216px;height:1.5px;background:var(--white)}

  /* category panel */
  .category-panel{position:absolute;left:330px;top:0;width:470px;height:675px;background:var(--panel-grey)}
  .breadcrumb-line{position:absolute;left:330px;top:80px;width:178px;height:5px;background:var(--lime)}
  .breadcrumb{position:absolute;left:516px;top:77px;font-size:10.5px;font-weight:500;letter-spacing:1.8px;color:var(--lime)}
  .category-pill{position:absolute;left:410px;top:151px;width:319px;height:54px;border:2px solid var(--lime);border-radius:27px;display:flex;align-items:center;padding-left:44px;font-size:21px;font-weight:600;color:#454545;letter-spacing:.3px}
  .category-badge{position:absolute;left:387px;top:150px;width:55px;height:55px;border-radius:50%;background:var(--bar-dark)}
  .subservice{position:absolute;left:455px;display:flex;align-items:center;font-size:23px;color:var(--ink-soft)}
  .subservice__icon{width:42px;height:42px;border-radius:4px;background:var(--icon-tint);margin-right:13px;flex:none}

  /* description */
  .description{position:absolute;left:876px;top:70px;width:290px}
  .description__title{font-size:24px;font-weight:600;line-height:29px;color:var(--heading-green);margin-bottom:22px}
  .description p{font-size:14px;line-height:18.7px;margin-bottom:6px}
  .bullets{list-style:none;margin-top:2px}
  .bullets li{position:relative;padding-left:20px;font-size:14px;line-height:18.7px;margin-bottom:5.5px}
  .bullets li svg{position:absolute;left:2px;top:3px;width:12px;height:14px}

  /* brand mark */
  .brand{position:absolute;left:978px;top:623px;display:flex;align-items:center;gap:8px}
  .brand__dot{width:24px;height:24px;border-radius:50%;background:var(--lime)}
  .brand__name{font-size:16px;font-weight:600;color:var(--heading-green);letter-spacing:.5px}

  /* footer */
  .footer{position:absolute;left:0;top:632px;height:27px;display:flex}
  .footer__page{width:60px;background:var(--olive);color:var(--white);font-size:17px;font-weight:700;display:flex;align-items:center;justify-content:center}
  .footer__trail{width:613px;background:var(--bar-dark);color:var(--white);font-size:15px;display:flex;align-items:center;padding-left:12px;letter-spacing:.3px}
  .footer__trail b{font-weight:700}
  .footer__trail .current{color:var(--lime);font-weight:700}
</style>
</head>
<body>
<div class="slide">

  <nav class="service-nav">
    <div class="service-nav__title">OUR SERVICES</div>
    <div class="service-nav__rule"></div>

    <div class="service-item service-item--active" style="top:139px;height:83px">
      <svg class="service-item__icon" viewBox="0 0 36 40" fill="none" stroke="#fff" stroke-width="2">
        <circle cx="18" cy="16" r="9" fill="#fff"/>
        <rect x="14" y="26" width="8" height="6" fill="#fff"/>
        <line x1="15" y1="35" x2="21" y2="35"/>
        <line x1="18" y1="1" x2="18" y2="4"/><line x1="3" y1="16" x2="6" y2="16"/><line x1="30" y1="16" x2="33" y2="16"/>
        <line x1="7" y1="5" x2="9" y2="7"/><line x1="29" y1="5" x2="27" y2="7"/>
      </svg>
      <span>Research &amp;<br>Strategy</span>
    </div>

    <div class="service-item" style="top:236px;height:50px">
      <svg class="service-item__icon" viewBox="0 0 36 40" fill="none" stroke="#fff" stroke-width="3">
        <circle cx="18" cy="6" r="3"/><line x1="18" y1="9" x2="18" y2="36"/>
        <line x1="11" y1="15" x2="25" y2="15"/>
        <path d="M4 24 Q8 36 18 36 Q28 36 32 24"/>
      </svg>
      <span>Business<br>Development</span>
    </div>
    <div class="service-divider" style="top:305px"></div>

    <div class="service-item" style="top:322px;height:45px">
      <svg class="service-item__icon" viewBox="0 0 36 40" fill="none" stroke="#fff" stroke-width="2.5">
        <path d="M13 3 H23 M14 3 V15 L4 36 H32 L22 15 V3"/>
        <path d="M8 28 H28 L31 35 H5 Z" fill="#fff"/>
      </svg>
      <span>Venture Building</span>
    </div>
    <div class="service-divider" style="top:389px"></div>

    <div class="service-item" style="top:405px;height:45px">
      <svg class="service-item__icon" viewBox="0 0 36 40" fill="none" stroke="#fff" stroke-width="3.5">
        <circle cx="21" cy="14" r="10"/><line x1="13" y1="22" x2="4" y2="33" stroke-linecap="round" stroke-width="5"/>
      </svg>
      <span>Sustainable Due<br>Diligence</span>
    </div>
    <div class="service-divider" style="top:472px"></div>

    <div class="service-item" style="top:488px;height:45px">
      <svg class="service-item__icon" viewBox="0 0 36 40">
        <path d="M12 4 H24 L21 11 Q32 18 32 28 Q32 37 18 37 Q4 37 4 28 Q4 18 15 11 Z" fill="#fff"/>
        <text x="18" y="31" text-anchor="middle" font-family="Fira Sans,sans-serif" font-size="13" fill="#a6c83a">$</text>
      </svg>
      <span>Expansion<br>Advisory</span>
    </div>
    <div class="service-divider" style="top:555px"></div>
  </nav>

  <section class="category-panel"></section>
  <div class="breadcrumb-line"></div>
  <div class="breadcrumb">SERVICES &gt;&gt; RESEARCH &amp; STRATEGY</div>

  <div class="category-pill">RESEARCH &amp; STRATEGY</div>
  <div class="category-badge" role="img" aria-label="Research and strategy emblem with compass and magnifier"></div>

  <div class="subservice" style="top:244px"><div class="subservice__icon" role="img" aria-label="Scenario planning icon"></div>Scenario Planning</div>
  <div class="subservice" style="top:311px"><div class="subservice__icon" role="img" aria-label="Market analysis icon"></div>Market Analysis</div>
  <div class="subservice" style="top:380px"><div class="subservice__icon" role="img" aria-label="Expert survey icon"></div>Expert Survey</div>
  <div class="subservice" style="top:449px"><div class="subservice__icon" role="img" aria-label="Start-up screening icon"></div>Start-up Screening</div>

  <section class="description">
    <h1 class="description__title">Research + Strategy<br>for Innovation &amp;<br>Growth.</h1>
    <p>Consectetuer elit adipiscing, sed diam nonummy ex nibh. Euismod tincidunt ut laoreet dolore magna aliquam erat.</p>
    <p>Exerci ottatation ullamcorper suscipit lobortis nisl ut nonummy aliquip exea commodo.</p>
    <ul class="bullets">
      <li><svg viewBox="0 0 12 14"><path d="M1 1 L11 7 L1 13 Z" fill="none" stroke="#a6c83a" stroke-width="1.3"/></svg>Lorem ipsum dolor sit amet laoreet aliquae ullamcorper</li>
      <li><svg viewBox="0 0 12 14"><path d="M1 1 L11 7 L1 13 Z" fill="none" stroke="#a6c83a" stroke-width="1.3"/></svg>Conseceur elit adisponti aed diam nonummy exea</li>
      <li><svg viewBox="0 0 12 14"><path d="M1 1 L11 7 L1 13 Z" fill="none" stroke="#a6c83a" stroke-width="1.3"/></svg>Euismod tincidunt ut laoreet dolore nisl adipiscing</li>
      <li><svg viewBox="0 0 12 14"><path d="M1 1 L11 7 L1 13 Z" fill="none" stroke="#a6c83a" stroke-width="1.3"/></svg>Magna aliquam erat nibh ex ead commodo laoreet</li>
      <li><svg viewBox="0 0 12 14"><path d="M1 1 L11 7 L1 13 Z" fill="none" stroke="#a6c83a" stroke-width="1.3"/></svg>Exerci tation ullamcorper suscipit lobortis diam</li>
    </ul>
  </section>

  <div class="brand">
    <div class="brand__dot"></div>
    <div class="brand__name">TALVORA PARTNERS</div>
  </div>

  <footer class="footer">
    <div class="footer__page">03</div>
    <div class="footer__trail">SMART MOBILITY &amp; KDR&nbsp;&gt;&gt;&nbsp;<b>SERVICES</b>&nbsp;&gt;&gt;&nbsp;<span class="current">RESEARCH &amp; STRATEGY</span></div>
  </footer>

</div>
</body>
</html>
```